Packaging and labelling for Swiss made Organic CBD Oil

Visit our website www.clearleafmerida.example
We have not put any product on yet as require packaging and label design .
Website will give you a great feel for the company and how we have used
the logo . The Vextora cbd product shown is a company similar to ourselves with similar core values , we liked the clean packaging design they have .

Im happy if you want use the mandala symbol in our logo separate from
KELVORA, to separate and use the mandala symbol as a larger icon than
it appears in our logo
Clean , Pure , organic feel. Like the product to look pharmaceutical and life changing not gimmicky.
Colours to go with or be the same as our logo colours
But not too cold and clinical
Bottle size 84mm x 25mm
Label size 75mm x 30mm
Box 30mm x 30mm x 100mm
6 products
Full Spectrum :
500mg CBD (5%)
1000mg CBD ( 10% )
1500mg CBD (15%)
2000mg CBD ( 20% )
Broad spectrum THC Free
500mg CBD (5%)
Pets
500mg Broad Spectrum THC Free
Updates

Would like the design to be more modern than traditional

LABEL Information Front of Bottle - Logo KELVORA & Mandala - Mandala can be used separately as design symbol Organic Cannabis Oil 1500mg CBD (15%) Ful Spectrum 10ml Back of bottle Ingredients: Organic Cannabis Oil Extract Organic Sunflower Seed Oil THC - 0.2% Certified Swiss Organic Cultivation Shake well before use. Store in a cool , dry place and out of the each of children BOX information Front and rear Logo - KELVORA & Mandala - Mandala can be used separately as a design symbol Organic Cannabis Oil 1500mg CBD (15%) Full Spectrum Sides x 2 This product is a food supplement and is not intended to diagnose, treat, cure or prevent any disease If you are pregnant, lactating or taking any medication consult your health care practitioner Suitable for vegetarians and vegans Ingredients Organic Cannabis Oil extract Organis Sunflower Oil Store in a cool ,dry place, out of the reach of children Recommended Use 1-5 drops ( 1 drop = 7.5mg CBD ) Subject to body weight and personal requirement - visit www.clearleafmerida for more information 100% Natural 100% Organic GMO free 100% Vegan ( symbol with each ) Expiry date see bottle label Cultivated and manufactured in Switzerland

Target Market(s)

age 40 - 80

Font styles to use
Other font styles liked:
• In our website we have used Open Sans for the copy and Lato for headings .

Requirements
Must have
• look like an Industry leader
Kelvora will change the quality of peoples lives and in some cases may
even save lives so want look powerful and credible
Our Mission is - Through Delivering Pure , Premium , Organic products we will educate, inform and help people achieve healthier , happier lifestyles
Nice to have
• Colours to look good with our logo colours or be the same as our logo
colours
Logo Font - Avenir Black and Avenir Book

Font used in website - Content - Open Sans / Headings - Lato
If you have another font for the packaging information that will go well with
our logo, I'm happy for you to use your skills

```html
<!DOCTYPE html>
<html lang="en">
<head>
<meta charset="utf-8">
<title>Kelvora Pet CBD Oil – Label and Box Sides</title>
<link rel="stylesheet" href="https://fonts.googleapis.com/css2?family=Open+Sans:wght@300;400;600;700&display=swap">
<style>
  :root {
    --paper: #ffffff;
    --guide: #5ce1ea;
    --panel-dark: #5e5f62;
    --panel-mid: #9c9da1;
    --panel-flat: #6d6e70;
    --ink-light: #f4f4f4;
    --ink-caption: #111111;
    --teal: #8fd6d6;
    --organic-green: #7dbb4a;
    --swiss-red: #e2231a;
  }
  html, body {
    margin: 0;
    padding: 0;
    width: 1200px;
    height: 1000px;
    overflow: hidden;
    background: var(--paper);
  }
  .artboard { display: block; width: 1200px; height: 1000px; }
  .caption { font-family: "Open Sans", sans-serif; font-weight: 400; font-size: 18px; fill: var(--ink-caption); }
  .brand-name { font-family: "Open Sans", sans-serif; font-weight: 700; fill: var(--ink-light); letter-spacing: 1px; }
  .product-title { font-family: "Open Sans", sans-serif; font-weight: 300; fill: var(--ink-light); }
  .copy { font-family: "Open Sans", sans-serif; font-weight: 300; fill: var(--ink-light); }
  .copy-strong { font-weight: 600; }
  .copy-teal { font-family: "Open Sans", sans-serif; font-weight: 600; fill: var(--teal); }
  .icon-label { font-family: "Open Sans", sans-serif; font-weight: 600; font-size: 9.5px; fill: var(--teal); }
  .icon-ring { fill: none; stroke: var(--teal); stroke-width: 2.4; }
  .icon-glyph { fill: var(--teal); }
  .guide { stroke: var(--guide); stroke-width: 1; }
</style>
</head>
<body>
<svg class="artboard" viewBox="0 0 1200 1000" xmlns="http://www.w3.org/2000/svg">
  <defs>
    <linearGradient id="box-sheen" x1="0" y1="0" x2="1" y2="0">
      <stop offset="0" stop-color="#606164"/>
      <stop offset="0.5" stop-color="#96979b"/>
      <stop offset="0.62" stop-color="#9c9da1"/>
      <stop offset="1" stop-color="#56575a"/>
    </linearGradient>
    <linearGradient id="label-sheen" x1="0" y1="0" x2="1" y2="0">
      <stop offset="0" stop-color="#5b5c5f"/>
      <stop offset="0.6" stop-color="#a0a1a5"/>
      <stop offset="1" stop-color="#56575a"/>
    </linearGradient>
    <radialGradient id="symbol-glow" cx="0.5" cy="0.5" r="0.5">
      <stop offset="0" stop-color="#a9c7c7" stop-opacity="0.28"/>
      <stop offset="1" stop-color="#a9c7c7" stop-opacity="0"/>
    </radialGradient>
    <radialGradient id="symbol-teal" cx="0.5" cy="0.5" r="0.5">
      <stop offset="0" stop-color="#8fd6d6" stop-opacity="0.55"/>
      <stop offset="1" stop-color="#8fd6d6" stop-opacity="0"/>
    </radialGradient>
  </defs>

  <!-- Captions -->
  <text class="caption" x="670" y="380" text-anchor="middle">Box sides</text>
  <text class="caption" x="246" y="598" text-anchor="middle">Label for bottle</text>

  <!-- Box top panel -->
  <g class="box-top">
    <rect x="833" y="43" width="336" height="337" fill="var(--panel-flat)" stroke="#d0d0d0" stroke-width="1"/>
    <rect x="916" y="136" width="170" height="150" fill="url(#symbol-teal)" role="img" aria-label="Brand mandala symbol"/>
  </g>

  <!-- Box sides -->
  <g class="box-sides">
    <rect x="497" y="398" width="672" height="560" fill="url(#box-sheen)" stroke="#d0d0d0" stroke-width="1"/>
    <rect x="510" y="470" width="659" height="480" fill="url(#symbol-glow)" role="img" aria-label="Large faint mandala petals decoration"/>

    <!-- Front panel -->
    <g class="box-front">
      <text class="brand-name" x="523" y="463" font-size="23">KELVORA</text>
      <rect x="515" y="673" width="89" height="18" fill="var(--organic-green)"/>
      <rect x="607" y="673" width="18" height="18" fill="var(--swiss-red)"/>
      <text class="product-title" x="514" y="721" font-size="27">Pet CBD Oil</text>
      <text class="product-title" x="514" y="874" font-size="17">500 mg CBD (5%)</text>
      <text class="product-title" x="514" y="898" font-size="17">Broad Spectrum</text>
      <text class="product-title" x="515" y="942" font-size="15">Made in Switzerland</text>
    </g>

    <!-- Information panel -->
    <g class="box-info copy" font-size="11">
      <text x="677" y="627">This product is a food</text>
      <text x="677" y="639">supplement and is not</text>
      <text x="677" y="651">intended to diagnose, treat,</text>
      <text x="677" y="663">cure or prevent any disease.</text>
      <text x="677" y="684">If your pet is on any</text>
      <text x="677" y="696">medication consult your</text>
      <text x="677" y="708">veterinarian.</text>
      <text x="677" y="729"><tspan class="copy-strong">Ingredients:</tspan> Organic Cannabis</text>
      <text x="677" y="741">Oil Extract, Organic Sunflower</text>
      <text x="677" y="753">Seed Oil</text>
      <text x="746" y="777" text-anchor="middle" font-size="16">THC Free</text>
      <text x="677" y="798">Store in a cool, dry place, out</text>
      <text x="677" y="810">of the reach of children.</text>
      <text class="copy-teal" x="677" y="832" font-size="12">Batch No and Lab Results</text>
      <text x="677" y="846">Visit <tspan class="copy-strong" font-size="9.5">www.kelvoraorganic.example</tspan></text>
      <text x="677" y="858">for independent third party</text>
      <text x="677" y="870">lab test results for this product</text>
      <text x="677" y="890">Batch No and expiry date see</text>
      <text x="677" y="902">label on bottom of box</text>
      <text x="749" y="942" text-anchor="middle" font-size="14">10 ml</text>
    </g>

    <!-- Rear panel -->
    <g class="box-rear">
      <text class="brand-name" x="860" y="463" font-size="23">KELVORA</text>
      <rect x="852" y="673" width="89" height="18" fill="var(--organic-green)"/>
      <rect x="944" y="673" width="18" height="18" fill="var(--swiss-red)"/>
      <text class="product-title" x="850" y="721" font-size="27">Pet CBD Oil</text>
      <text class="product-title" x="851" y="874" font-size="17">500 mg CBD (5%)</text>
      <text class="product-title" x="851" y="898" font-size="17">Broad Spectrum</text>
      <text class="product-title" x="852" y="942" font-size="15">Made in Switzerland</text>
    </g>

    <!-- Usage and claims panel -->
    <g class="box-claims">
      <text class="copy-teal" x="1012" y="434" font-size="11.5">Recommended Use:</text>
      <g class="copy" font-size="11">
        <text x="1012" y="447">Shake well before use. 1 drop</text>
        <text x="1012" y="460">per 10 lbs of body weight,</text>
        <text x="1012" y="473">twice a day with food.</text>
        <text x="1012" y="486">(1 drop = 2.5mg CBD)</text>
        <text x="1012" y="499">Visit <tspan class="copy-strong" font-size="8.5">www.kelvoraorganic.example</tspan></text>
        <text x="1012" y="512">for more information.</text>
      </g>

      <g class="claim-natural">
        <circle class="icon-ring" cx="1084" cy="569" r="25"/>
        <path class="icon-glyph" d="M1084 551 L1088 566 L1100 560 L1090 572 L1084 586 L1078 572 L1068 560 L1080 566 Z"/>
        <text class="icon-label" x="1084" y="606" text-anchor="middle">100% Natural</text>
      </g>
      <g class="claim-organic">
        <circle class="icon-ring" cx="1084" cy="651" r="25"/>
        <path class="icon-glyph" d="M1078 638 C1070 646 1072 656 1080 658 C1086 652 1086 644 1078 638 Z M1068 664 C1078 668 1090 668 1100 656 C1094 656 1088 660 1082 662 L1068 660 Z"/>
        <text class="icon-label" x="1084" y="689" text-anchor="middle">100% Organic</text>
      </g>
      <g class="claim-vegan">
        <circle class="icon-ring" cx="1084" cy="738" r="25"/>
        <rect class="icon-glyph" x="1071" y="724" width="3" height="28" rx="1.5"/>
        <rect class="icon-glyph" x="1079" y="724" width="3" height="28" rx="1.5"/>
        <path class="icon-glyph" d="M1092 752 L1092 736 C1088 734 1087 728 1090 724 L1092 729 L1094 724 L1096 729 L1098 724 C1101 728 1100 734 1095 736 L1095 752 Z"/>
        <text class="icon-label" x="1084" y="775" text-anchor="middle">100% Vegan</text>
      </g>
      <g class="claim-gmo-free">
        <circle class="icon-ring" cx="1084" cy="823" r="25"/>
        <path class="icon-glyph" d="M1080 808 L1088 808 L1088 812 L1086 812 L1086 820 L1096 836 L1072 836 L1082 820 L1082 812 L1080 812 Z"/>
        <line x1="1070" y1="840" x2="1100" y2="808" stroke="var(--teal)" stroke-width="2.4"/>
        <text class="icon-label" x="1084" y="861" text-anchor="middle">GMO Free</text>
      </g>

      <text class="product-title" x="1084" y="923" text-anchor="middle" font-size="16">THC Free</text>
      <text class="product-title" x="1084" y="942" text-anchor="middle" font-size="14">10 ml</text>
    </g>
  </g>

  <!-- Bottle label -->
  <g class="bottle-label">
    <rect x="31" y="617" width="420" height="168" fill="url(#label-sheen)" stroke="#d0d0d0" stroke-width="1"/>
    <rect x="40" y="630" width="170" height="150" fill="url(#symbol-glow)" role="img" aria-label="Faint mandala symbol decoration"/>
    <text class="brand-name" x="78" y="648" font-size="18">KELVORA</text>
    <rect x="79" y="687" width="62" height="12" fill="var(--organic-green)"/>
    <rect x="145" y="687" width="12" height="12" fill="var(--swiss-red)"/>
    <text class="product-title" x="77" y="718" font-size="19">Pet CBD Oil</text>
    <text class="product-title" x="78" y="753" font-size="12">500 mg CBD (5%)</text>
    <text class="product-title" x="78" y="767" font-size="12">Broad Spectrum</text>

    <g class="label-back copy" font-size="10">
      <text transform="translate(221,773) rotate(-90)"><tspan class="copy-strong">Ingredients:</tspan> Organic Cannabis</text>
      <text transform="translate(233,773) rotate(-90)">Oil Extract, Organic Sunflower</text>
      <text transform="translate(245,773) rotate(-90)">Seed Oil</text>
      <text transform="translate(267,773) rotate(-90)">Certified Swiss Organic</text>
      <text transform="translate(279,773) rotate(-90)">Cultivation and 100% Natural</text>
      <text transform="translate(291,773) rotate(-90)">THC Free</text>
      <text transform="translate(316,773) rotate(-90)">Shake well before use. Store</text>
      <text transform="translate(328,773) rotate(-90)">in a cool, dry place, out of the</text>
      <text transform="translate(340,773) rotate(-90)">reach of children.</text>
      <text class="copy-teal" transform="translate(363,773) rotate(-90)">Recommended Use:</text>
      <text transform="translate(375,773) rotate(-90)">1 drop per 10 lbs of body</text>
      <text transform="translate(387,773) rotate(-90)">weight, twice a day with food.</text>
      <text transform="translate(399,773) rotate(-90)">Visit <tspan class="copy-strong" font-size="8.5">www.kelvoraorganic.example</tspan></text>
      <text transform="translate(411,773) rotate(-90)">for more information.</text>
      <text transform="translate(443,721) rotate(-90)" font-size="13">10 ml</text>
    </g>
  </g>

  <!-- Fold guides -->
  <g class="fold-guides">
    <line class="guide" x1="42.5" y1="32" x2="42.5" y2="968"/>
    <line class="guide" x1="210.5" y1="32" x2="210.5" y2="968"/>
    <line class="guide" x1="665.5" y1="32" x2="665.5" y2="968"/>
    <line class="guide" x1="833.5" y1="32" x2="833.5" y2="968"/>
    <line class="guide" x1="1000.5" y1="32" x2="1000.5" y2="968"/>
  </g>
</svg>
</body>
</html>
```